Corvane Holdings , new business card design

investment firm with corporate clients . need double sided business card , vertical and horizontal options ,logo must be clear. prefer pantone colors only and sharp design. website also www.corvane.ae

Khalid Bin Tarrafi
Managing Director
Tel. +971 4 387 2940
Mobile +971 50 518 2403
khalid@corvane.ae
Q-Span Plaza, officw 18-B07, Warqa Gardens, Dubai

Contact Information for Business Card

Khalid Bin Tarrafi
Managing Director

Font styles to use
Serif

Colors

Designer to choose colors to be used in the design.

```html
<!DOCTYPE html>
<html lang="en">
<head>
<meta charset="utf-8">
<title>Corvane Holdings – Business Card</title>
<link rel="stylesheet" href="https://fonts.googleapis.com/css2?family=Roboto+Condensed:wght@300;400;700&display=swap">
<style>
  :root {
    --stage: #e9e8e6;
    --paper: #f7f7f5;
    --ink: #111218;
    --steel-blue: #4a76a0;
    --steel-blue-deep: #3f6890;
    --white: #ffffff;
  }
  * { box-sizing: border-box; margin: 0; padding: 0; }
  html, body { width: 1200px; height: 911px; overflow: hidden; }
  body {
    background: var(--stage);
    font-family: "Roboto Condensed", Arial, sans-serif;
    position: relative;
  }
  .card {
    position: absolute;
    width: 540px;
    height: 310px;
    box-shadow: 0 10px 30px rgba(0,0,0,.18);
    overflow: hidden;
  }
  /* Front */
  .card--front { left: 40px; top: 300px; background: var(--paper); }
  .front__identity {
    position: absolute; left: 0; top: 0; width: 100%; height: 190px;
    display: flex; flex-direction: column; align-items: center; justify-content: center;
  }
  .wordmark {
    font-weight: 300;
    font-size: 34px;
    letter-spacing: 8px;
    text-transform: uppercase;
    color: var(--ink);
    display: flex; align-items: center; gap: 14px;
  }
  .wordmark__square { width: 12px; height: 12px; background: var(--steel-blue); }
  .person { margin-top: 26px; text-align: center; }
  .person__name {
    font-weight: 700; font-size: 19px; color: var(--steel-blue);
    text-transform: uppercase; letter-spacing: .3px;
  }
  .person__title {
    font-weight: 400; font-size: 13px; color: var(--ink);
    text-transform: uppercase; letter-spacing: .6px; margin-top: 2px;
  }
  .front__contact-band {
    position: absolute; left: 0; top: 190px; width: 100%; height: 78px;
    background: var(--ink); color: var(--white);
    border-bottom: 4px solid var(--paper);
    display: flex; flex-direction: column; justify-content: center;
    padding-left: 64px; font-size: 13px; line-height: 1.7;
  }
  .front__contact-band b { font-weight: 700; }
  .front__address-band {
    position: absolute; left: 0; top: 268px; width: 100%; height: 42px;
    background: var(--steel-blue); color: var(--white);
    display: flex; align-items: center; padding-left: 64px;
    font-size: 12.5px; font-weight: 300; letter-spacing: .3px;
  }
  /* Back */
  .card--back { left: 620px; top: 300px; background: var(--steel-blue); }
  .back__wordmark {
    position: absolute; inset: 0;
    display: flex; align-items: center; justify-content: center;
  }
  .back__wordmark .wordmark { color: var(--ink); }
  .back__wordmark .wordmark__square { background: var(--white); }
  .back__website {
    position: absolute; left: 0; bottom: 30px; width: 100%;
    text-align: center; color: var(--white);
    font-size: 11px; font-weight: 300; letter-spacing: 9px;
  }
</style>
</head>
<body>
  <section class="card card--front" aria-label="Business card front">
    <div class="front__identity">
      <div class="wordmark"><span>Corvane Holdings</span><span class="wordmark__square"></span></div>
      <div class="person">
        <p class="person__name">Khalid Bin Tarrafi</p>
        <p class="person__title">Managing Director</p>
      </div>
    </div>
    <div class="front__contact-band">
      <p><b>P :</b> +971 4 387 2940 &nbsp;<b>C :</b> +971 50 518 2403</p>
      <p><b>E :</b> khalid@corvane.ae &nbsp;<b>W :</b> www.corvane.ae</p>
    </div>
    <div class="front__address-band">Q-Span Plaza, officw 18-B07, Warqa Gardens, Dubai</div>
  </section>

  <section class="card card--back" aria-label="Business card back">
    <div class="back__wordmark">
      <div class="wordmark"><span>Corvane Holdings</span><span class="wordmark__square"></span></div>
    </div>
    <p class="back__website">www.corvane.ae</p>
  </section>
</body>
</html>
```